Request for Business Card Design

Hi. My name is Marlene, I am looking for a new business card design for my company, Quarrow Signal Instruments, LLC. I really like the design you did for Tarsel Venture and was hoping you could do something similar using our full logo and our mark. I am also open to any raised texture design using our mark. I have attached our full logo, which would need to be somewhere on the card, as well as the mark in both outline and full form, as well as our brand colors / guide. The card does not have to be white, as long as our logo and mark appear. I actually like darker colored business cards more, but am open to all options. If you are interested in working with me, please let me know. We would also take the business card design into letterhead design if you can do that.

```html
<!DOCTYPE html>
<html lang="en">
<head>
<meta charset="utf-8">
<title>Quarrow Signal Instruments — Business Card</title>
<link href="https://fonts.googleapis.com/css2?family=Poppins:wght@400;600;700&display=swap" rel="stylesheet">
<style>
  :root {
    --page: #e9e9e7;
    --card: #161616;
    --accent: #0a9cc6;
    --band-grey: #3d3e41;
    --ink-light: #ffffff;
    --shadow: rgba(0, 0, 0, 0.28);
  }
  * { box-sizing: border-box; margin: 0; padding: 0; }
  html, body {
    width: 1200px; height: 900px; overflow: hidden;
    background: var(--page);
    font-family: "Poppins", sans-serif;
  }
  .canvas { position: relative; width: 1200px; height: 900px; }
  .card {
    position: absolute; width: 620px; height: 354px;
    background: var(--card); overflow: hidden;
    box-shadow: 0 14px 30px var(--shadow);
  }
  .card--front { left: 80px; top: 80px; }
  .card--back { left: 500px; top: 466px; }

  .brand { display: flex; align-items: center; gap: 16px; color: var(--ink-light); font-weight: 700; }
  .brand__dot { border-radius: 50%; border: 9px solid var(--accent); flex: none; }
  .brand__name { line-height: 1; letter-spacing: 0.06em; text-transform: uppercase; }
  .brand__tagline { line-height: 1.2; letter-spacing: 0.04em; text-transform: uppercase; }

  .card--front .brand { position: absolute; left: 50%; top: 50%; transform: translate(-50%, -50%); }
  .card--front .brand__dot { width: 74px; height: 74px; }
  .card--front .brand__name { font-size: 48px; }
  .card--front .brand__tagline { font-size: 13px; margin-top: 6px; }

  .card--back .brand { position: absolute; right: 34px; top: 46px; gap: 12px; }
  .card--back .brand__dot { width: 52px; height: 52px; border-width: 7px; }
  .card--back .brand__name { font-size: 34px; }
  .card--back .brand__tagline { font-size: 9.5px; margin-top: 4px; }

  .person { position: absolute; left: 50px; top: 72px; }
  .person__name { color: var(--accent); font-size: 23px; font-weight: 600; letter-spacing: 0.02em; line-height: 1.1; text-transform: uppercase; }
  .person__title { color: var(--ink-light); font-size: 15px; font-weight: 400; }

  .contact { position: absolute; left: 84px; top: 166px; color: var(--ink-light); font-size: 15px; line-height: 1.45; }
  .contact__row { display: flex; align-items: center; gap: 12px; }
  .contact__icon { width: 20px; height: 20px; fill: var(--accent); flex: none; }
  .contact__address { margin-top: 20px; padding-left: 32px; font-size: 16px; line-height: 1.4; }

  .wave { position: absolute; left: 0; top: 0; width: 620px; height: 354px; }
  .website { position: absolute; right: 36px; top: 246px; color: var(--ink-light); font-size: 14px; }
</style>
</head>
<body>
<main class="canvas">

  <section class="card card--front" aria-label="Card front">
    <div class="brand">
      <span class="brand__dot"></span>
      <div>
        <div class="brand__name">Quarrow</div>
        <div class="brand__tagline">Signal Instruments</div>
      </div>
    </div>
  </section>

  <section class="card card--back" aria-label="Card back">
    <svg class="wave" viewBox="0 0 620 354" aria-hidden="true">
      <path fill="var(--band-grey)" d="M0 290 C170 296 290 290 390 225 C470 172 550 148 620 138 L620 354 L0 354 Z"/>
      <path fill="var(--accent)" d="M0 316 C190 320 320 300 420 222 C490 168 560 146 620 132 L620 354 L0 354 Z"/>
    </svg>

    <div class="person">
      <div class="person__name">Elias Varden</div>
      <div class="person__title">Managing Director</div>
    </div>

    <div class="brand">
      <span class="brand__dot"></span>
      <div>
        <div class="brand__name">Quarrow</div>
        <div class="brand__tagline">Signal Instruments</div>
      </div>
    </div>

    <div class="contact">
      <div class="contact__row">
        <svg class="contact__icon" viewBox="0 0 24 24" aria-hidden="true"><path d="M6.6 10.8a15.1 15.1 0 0 0 6.6 6.6l2.2-2.2a1 1 0 0 1 1-.25 11.4 11.4 0 0 0 3.6.57 1 1 0 0 1 1 1V20a1 1 0 0 1-1 1A17 17 0 0 1 3 4a1 1 0 0 1 1-1h3.5a1 1 0 0 1 1 1c0 1.250.2 2.450.57 3.57a1 1 0 0 1-.25 1z"/></svg>
        <span>044-318 702 615</span>
      </div>
      <div class="contact__row">
        <svg class="contact__icon" viewBox="0 0 24 24" aria-hidden="true"><path d="M2 5h20v14H2z" fill="var(--accent)"/><path d="M3 6l9 7 9-7" fill="none" stroke="var(--card)" stroke-width="1.6"/></svg>
        <span>elias@quarrow.com</span>
      </div>
      <div class="contact__address">87, Fennick Row, Suite 4<br>Lindmere, 30718</div>
    </div>

    <div class="website">www.quarrowsignal.com</div>
  </section>

</main>
</body>
</html>
```